4th Generation Family Business Needs a New Card Design!

We are a family owned 4th Generation company. We are based in the Sydney, Australia area and we are desperately in need of a more modern and classy card. We are monumental masons who design, supply & erect lasting memorials throughout cemeteries in Sydney. Our customers are normally in a period of grieving. I have attached logo files that will need to be implemented on the card. Company was established 1935. Australian Owned and Operated. Card needs to be designed to PIXO.com specification.

Target Market(s)

Our target market is based upon people that a grieving for family members that have passed away. We also deal with alot of companies that own and operate cemeteries.

Industry/Entity Type

Business

Contact Information for Business Card

Simon Harcourt, Operations Manager, 0417293086, simon@harcourtmemorials.com.au
Lewis Harcourt, Director, 0491630572, lewis@harcourtmemorials.com.au
Phone # 02 9561 3048
Website: www.harcourtmemorials.com.au
Address: Suite 17, 8 Palfrey Lane, West Carlow, Sydney NSW 2156

Font styles to use
Serif
Decorative
Script

Requirements
Must have
• Would like to see the logo nicely implemented with a modern design. Embossed lettering would be a nice additive.

```html
<!DOCTYPE html>
<html lang="en">
<head>
<meta charset="utf-8">
<title>Harcourt Memorials – Business Card</title>
<link rel="stylesheet" href="https://fonts.googleapis.com/css2?family=Open+Sans:ital,wght@0,600;1,400;1,700;1,800&display=swap">
<style>
  :root {
    --backdrop: #e4e3e1;
    --card: #fffdfb;
    --ink: #1c1a19;
    --ink-soft: #2b2927;
    --shadow: rgba(0, 0, 0, 0.18);
  }
  * { box-sizing: border-box; margin: 0; padding: 0; }
  html, body {
    width: 1200px;
    height: 675px;
    overflow: hidden;
    background: var(--backdrop);
  }
  .canvas {
    position: relative;
    width: 1200px;
    height: 675px;
    display: flex;
    align-items: center;
    justify-content: center;
    gap: 90px;
  }
  .card {
    position: relative;
    width: 460px;
    height: 281px;
    background: var(--card);
    box-shadow: 0 6px 18px var(--shadow);
    color: var(--ink);
    font-family: "Open Sans", sans-serif;
  }

  /* Front: contact details */
  .card-front .details {
    position: absolute;
    top: 92px;
    left: 0;
    right: 0;
    display: flex;
    justify-content: center;
    gap: 20px;
    font-style: italic;
    font-size: 10.5px;
    line-height: 1.32;
  }
  .person {
    text-align: right;
  }
  .person-name {
    font-weight: 800;
    font-size: 15px;
    letter-spacing: 0.02em;
    text-transform: uppercase;
    line-height: 1.05;
    margin-bottom: 1px;
  }
  .contact {
    padding-top: 3px;
    color: var(--ink-soft);
  }
  .contact .label {
    font-weight: 700;
    margin-right: 3px;
  }
  .contact .web {
    font-weight: 700;
    color: var(--ink);
  }

  /* Back: company name */
  .card-back {
    display: flex;
    align-items: center;
    justify-content: center;
  }
  .brand {
    display: flex;
    align-items: center;
    gap: 10px;
    font-family: "Open Sans", sans-serif;
    font-weight: 600;
    font-size: 24px;
    letter-spacing: 0.06em;
    text-transform: uppercase;
    color: var(--ink);
  }
  .brand-mark {
    width: 14px;
    height: 14px;
    background: var(--ink);
  }
</style>
</head>
<body>
  <main class="canvas">
    <section class="card card-front" aria-label="Business card front">
      <div class="details">
        <div class="person">
          <p class="person-name">Simon Harcourt</p>
          <p class="person-role">Operations Manager</p>
          <p class="address-line">Suite 17, 8 Palfrey Lane</p>
          <p class="address-line">West Carlow, Sydney NSW 2156</p>
        </div>
        <div class="contact">
          <p><span class="label">C :</span>0417293086</p>
          <p><span class="label">P :</span>02 9561 3048</p>
          <p><span class="label">E :</span>simon@harcourtmemorials.com.au</p>
          <p class="web">www.harcourtmemorials.com.au</p>
        </div>
      </div>
    </section>

    <section class="card card-back" aria-label="Business card back">
      <div class="brand">
        <span class="brand-mark" aria-hidden="true"></span>
        <span class="brand-name">Harcourt Memorials</span>
      </div>
    </section>
  </main>
</body>
</html>
```